UI/ UX Design for ERP Software

We need a new UX/UI interface for a ERP software for property managers. Our CMMS / ERP solution is made based on responsive design technologies and is coded in PHP.
The overall UX to be similar to Tev Ulna - easy navigation, intuitive menus.

Industry/Entity Type

Property Management

Number of Pages Required

5+ page

Requirements
Must have
• Round dock buttons
Consistent icons across the application
Enough Spacing between buttons/icons/ menu
Consistent Font
Nice to have
• We would like the UX to allow the users to use the application without /minimum training.
Should not have
• we don't want anything that is classic with respect to UX

```html
<!DOCTYPE html>
<html lang="en">
<head>
<meta charset="utf-8">
<title>Domora – Active Dashboard</title>
<link href="https://fonts.googleapis.com/css2?family=Poppins:wght@400;500;600;700&display=swap" rel="stylesheet">
<style>
:root{
  --bg:#f3f4f7;
  --white:#ffffff;
  --side:#536078;
  --side-line:#64708a;
  --ink:#4a5467;
  --ink-soft:#9aa1ad;
  --blue:#1a9bfc;
  --blue-2:#3b82f6;
  --pill:#eef0f3;
  --up:#36b24a;
  --down:#f0364f;
  --grid:#eceef2;
}
*{box-sizing:border-box;margin:0;padding:0}
html,body{width:1200px;height:800px;overflow:hidden}
body{font-family:"Poppins",sans-serif;background:var(--bg);color:var(--ink);position:relative}
.topbar{position:absolute;left:0;top:0;width:1200px;height:89px;background:var(--white);box-shadow:0 2px 8px rgba(0,0,0,.04)}
.brand{position:absolute;left:40px;top:28px;display:flex;align-items:center;gap:8px;font-weight:600;font-size:26px;color:var(--blue-2)}
.brand-mark{width:20px;height:20px;border-radius:4px;background:var(--blue-2)}
.search{position:absolute;left:277px;top:27px;width:230px;height:36px;border-radius:18px;background:var(--pill);font-size:13px;color:var(--ink-soft);padding:9px 19px}
.search svg{position:absolute;right:16px;top:10px}
.sort{position:absolute;left:517px;top:27px;width:94px;height:36px;border-radius:18px;background:var(--pill);font-size:13px;color:var(--ink-soft);padding:9px 17px}
.sort svg{position:absolute;right:16px;top:15px}
.tool{position:absolute;top:23px;width:43px;height:43px;border-radius:8px;background:var(--pill);display:flex;align-items:center;justify-content:center}
.divider{position:absolute;left:1030px;top:26px;width:1px;height:37px;background:#e4e6ea}
.avatar{position:absolute;top:24px;width:41px;height:41px;border-radius:50%;border:2px solid var(--white)}
.avatar.add{background:var(--side);color:#fff;font-size:24px;display:flex;align-items:center;justify-content:center;font-weight:400}
.sidebar{position:absolute;left:0;top:89px;width:250px;height:711px;background:var(--side)}
.nav-active{position:absolute;left:19px;top:39px;width:201px;height:42px;border-radius:21px;background:linear-gradient(90deg,#1fa6f5,#2f8cf6);color:#fff;font-weight:600;font-size:16px;display:flex;align-items:center;gap:9px;padding-left:15px}
.nav-item{position:absolute;left:32px;width:182px;height:53px;color:#fff;font-size:13.5px;font-weight:500;display:flex;align-items:center;gap:10px;border-bottom:1px solid var(--side-line)}
.nav-item.last{border-bottom:none}
.nav-plus{position:absolute;right:-12px;top:18px;width:18px;height:18px;border-radius:50%;background:#7a849a;color:#fff;font-size:13px;line-height:18px;text-align:center}
.scroll-thumb{position:absolute;left:232px;top:294px;width:4px;height:67px;border-radius:2px;background:#3f4a5f}
.page-title{position:absolute;left:285px;top:124px;font-size:27px;font-weight:600;color:var(--ink)}
.stat{position:absolute;top:176px;width:169px;height:144px;background:var(--white);border-radius:6px;overflow:hidden}
.stat .delta{position:absolute;right:16px;top:14px;font-size:11px;font-weight:600}
.stat .delta.up{color:var(--up)}.stat .delta.down{color:var(--down)}
.stat .label{position:absolute;left:14px;top:37px;font-size:13px;color:var(--ink-soft)}
.stat .value{position:absolute;left:15px;top:55px;font-size:15px;font-weight:600;color:var(--ink)}
.stat svg.spark{position:absolute;left:0;bottom:0}
.panel{position:absolute;left:285px;top:343px;width:878px;height:374px;background:var(--white);border-radius:6px}
.range{position:absolute;left:27px;top:34px;display:flex;align-items:center;gap:9px;font-size:13px;color:var(--ink)}
.chip{position:absolute;top:31px;width:96px;height:25px;border-radius:13px;background:var(--pill);font-size:11px;font-weight:500;color:var(--ink);display:flex;align-items:center;justify-content:center;white-space:nowrap}
.legend{position:absolute;font-size:11.5px;font-weight:500;color:var(--ink);display:flex;align-items:center;gap:6px;white-space:nowrap}
.legend i{width:7px;height:7px;border-radius:50%;display:inline-block}
.footer{position:absolute;left:285px;width:878px;top:763px;text-align:center;font-size:14px;font-weight:500;color:var(--ink)}
</style>
</head>
<body>
<header class="topbar">
  <div class="brand"><span class="brand-mark"></span>Domora</div>
  <div class="search">Search...
    <svg width="17" height="17" viewBox="0 0 17 17"><circle cx="7" cy="7" r="5.5" fill="none" stroke="#2b3342" stroke-width="1.8"/><line x1="11" y1="11" x2="15.5" y2="15.5" stroke="#2b3342" stroke-width="1.8" stroke-linecap="round"/></svg>
  </div>
  <div class="sort">A-Z
    <svg width="9" height="6" viewBox="0 0 9 6"><path d="M1 1l3.5 3.5L8 1" fill="none" stroke="#2b3342" stroke-width="1.6"/></svg>
  </div>
  <div class="tool" style="left:837px">
    <svg width="22" height="22" viewBox="0 0 22 22"><path d="M5 16V10a6 6 0 0 1 12 0v6l2 2H3z" fill="none" stroke="#4a5467" stroke-width="1.6" stroke-linejoin="round"/><path d="M9 19a2 2 0 0 0 4 0" fill="none" stroke="#4a5467" stroke-width="1.6"/><circle cx="16" cy="5" r="3" fill="#f0364f"/></svg>
  </div>
  <div class="tool" style="left:899px">
    <svg width="22" height="22" viewBox="0 0 22 22"><path d="M3 4h16v11H9l-4 4v-4H3z" fill="none" stroke="#4a5467" stroke-width="1.6" stroke-linejoin="round"/><line x1="7" y1="8" x2="15" y2="8" stroke="#4a5467" stroke-width="1.6"/><line x1="7" y1="11" x2="13" y2="11" stroke="#4a5467" stroke-width="1.6"/></svg>
  </div>
  <div class="tool" style="left:962px">
    <svg width="22" height="22" viewBox="0 0 22 22"><path d="M2 5h7l2 2h9v11H2z" fill="none" stroke="#4a5467" stroke-width="1.6" stroke-linejoin="round"/><circle cx="12" cy="12" r="2.6" fill="none" stroke="#4a5467" stroke-width="1.5"/><line x1="14" y1="14" x2="16.5" y2="16.5" stroke="#4a5467" stroke-width="1.5"/></svg>
  </div>
  <div class="divider"></div>
  <div class="avatar" style="left:1056px;background:linear-gradient(135deg,#7bd3c7,#c0683b)" role="img" aria-label="Team member avatar"></div>
  <div class="avatar" style="left:1085px;background:linear-gradient(135deg,#c7b8f5,#e8c3a6)" role="img" aria-label="Team member avatar"></div>
  <div class="avatar add" style="left:1118px">+</div>
</header>

<nav class="sidebar">
  <div class="nav-active">
    <svg width="19" height="19" viewBox="0 0 20 20"><circle cx="10" cy="10" r="8" fill="none" stroke="#fff" stroke-width="1.8"/><path d="M10 10l4-3" stroke="#fff" stroke-width="1.8" stroke-linecap="round"/><circle cx="10" cy="10" r="1.4" fill="#fff"/></svg>
    Dashboard
  </div>
  <div class="nav-item" style="top:90px"><svg width="20" height="20" viewBox="0 0 20 20" fill="none" stroke="#fff" stroke-width="1.5"><circle cx="8" cy="7" r="3.5"/><path d="M1.5 18c0-4 3-6 6.5-6s6.5 2 6.5 6"/><path d="M13 3.5a3.5 3.5 0 0 1 0 7M15.5 12.5c2 .8 3 2.8 3 5.5"/></svg>Customers</div>
  <div class="nav-item" style="top:143px"><svg width="20" height="20" viewBox="0 0 20 20" fill="none" stroke="#fff" stroke-width="1.6" stroke-linejoin="round"><path d="M2 9l8-7 8 7M4 8v10h12V8"/></svg>Properties</div>
  <div class="nav-item" style="top:196px"><svg width="20" height="20" viewBox="0 0 20 20" fill="none" stroke="#fff" stroke-width="1.5" stroke-linejoin="round"><path d="M2 9l8-7 8 7M4 8v10h12V8"/><circle cx="10" cy="10" r="2"/><path d="M7 16c0-2 1.3-3 3-3s3 1 3 3"/></svg>Tenant</div>
  <div class="nav-item" style="top:249px"><svg width="20" height="20" viewBox="0 0 20 20" fill="none" stroke="#fff" stroke-width="1.5"><rect x="4" y="2" width="13" height="16" rx="1.5"/><circle cx="10.5" cy="8" r="2.3"/><path d="M6.5 14.5c0-2 1.8-3.3 4-3.3s4 1.3 4 3.3M2 6h3M2 10h3M2 14h3"/></svg>Contact</div>
  <div class="nav-item" style="top:302px"><svg width="20" height="20" viewBox="0 0 20 20" fill="none" stroke="#fff" stroke-width="1.5"><path d="M5 7a5 5 0 0 1 10 0z"/><circle cx="10" cy="10" r="3"/><path d="M3 19v-3c0-2 3-3 7-3s7 1 7 3v3z"/></svg>Contractors</div>
  <div class="nav-item" style="top:355px"><svg width="20" height="20" viewBox="0 0 20 20" fill="none" stroke="#fff" stroke-width="1.5"><circle cx="8" cy="7" r="3.5"/><path d="M1.5 18c0-4 3-6 6.5-6s6.5 2 6.5 6"/><path d="M13 3.5a3.5 3.5 0 0 1 0 7M15.5 12.5c2 .8 3 2.8 3 5.5"/></svg>Employees</div>
  <div class="nav-item" style="top:408px"><svg width="22" height="20" viewBox="0 0 22 20" fill="none" stroke="#fff" stroke-width="1.5"><rect x="5" y="2" width="15" height="16" rx="2"/><circle cx="6" cy="9" r="3.5"/><path d="M11 7h6M11 10h6M11 13h6"/></svg>Compliance Manag...</div>
  <div class="nav-item" style="top:461px"><svg width="20" height="20" viewBox="0 0 20 20" fill="none" stroke="#fff" stroke-width="1.5"><path d="M3 3l14 14M17 3L3 17"/><circle cx="4" cy="4" r="2.5"/><circle cx="16" cy="16" r="2.5"/></svg>Prevent. Mainten...<span class="nav-plus">+</span></div>
  <div class="nav-item" style="top:514px"><svg width="20" height="20" viewBox="0 0 20 20" fill="none" stroke="#fff" stroke-width="1.5"><rect x="3" y="2" width="14" height="16" rx="1"/><path d="M6 11l3 3 6-7"/></svg>Work Orders<span class="nav-plus">+</span></div>
  <div class="nav-item" style="top:567px"><svg width="20" height="20" viewBox="0 0 20 20" fill="none" stroke="#fff" stroke-width="1.5" stroke-linejoin="round"><path d="M1 3h3l2 10h10l2-7H5"/><circle cx="8" cy="17" r="1.5"/><circle cx="15" cy="17" r="1.5"/></svg>Purchase Orders</div>
  <div class="nav-item last" style="top:620px"><svg width="20" height="20" viewBox="0 0 20 20" fill="none" stroke="#fff" stroke-width="1.6" stroke-linejoin="round"><path d="M2 9l8-7 8 7M4 8v10h12V8"/></svg>Property Inspections</div>
  <div class="scroll-thumb"></div>
</nav>

<main>
  <h1 class="page-title">Active Dashboard</h1>

  <svg width="0" height="0" style="position:absolute">
    <defs>
      <linearGradient id="g-pink" x1="0" y1="0" x2="0" y2="1"><stop offset="0" stop-color="#f06bd0" stop-opacity=".35"/><stop offset="1" stop-color="#f06bd0" stop-opacity="0"/></linearGradient>
      <linearGradient id="g-orange" x1="0" y1="0" x2="0" y2="1"><stop offset="0" stop-color="#f7924a" stop-opacity=".35"/><stop offset="1" stop-color="#f7924a" stop-opacity="0"/></linearGradient>
      <linearGradient id="g-violet" x1="0" y1="0" x2="0" y2="1"><stop offset="0" stop-color="#a66ef5" stop-opacity=".35"/><stop offset="1" stop-color="#a66ef5" stop-opacity="0"/></linearGradient>
      <linearGradient id="g-green" x1="0" y1="0" x2="0" y2="1"><stop offset="0" stop-color="#2ed3a0" stop-opacity=".35"/><stop offset="1" stop-color="#2ed3a0" stop-opacity="0"/></linearGradient>
      <linearGradient id="g-blue" x1="0" y1="0" x2="0" y2="1"><stop offset="0" stop-color="#22a6f5" stop-opacity=".35"/><stop offset="1" stop-color="#22a6f5" stop-opacity="0"/></linearGradient>
    </defs>
  </svg>

  <div class="stat" style="left:285px"><span class="delta up">+09.84% ↗</span><div class="label">Properties</div><div class="value">3 homes</div>
    <svg class="spark" width="169" height="55" viewBox="0 0 169 55"><path d="M38 55c8-6 10-12 16-14s6-8 12-8 6 4 12-2 6-10 14-10 6 6 12 6 12-20 24-20 18 8 24 12 12-8 17-10V55z" fill="url(#g-pink)"/><path d="M38 55c8-6 10-12 16-14s6-8 12-8 6 4 12-2 6-10 14-10 6 6 12 6 12-20 24-20 18 8 24 12 12-8 17-10" fill="none" stroke="#f06bd0" stroke-width="1.6"/></svg></div>
  <div class="stat" style="left:463px"><span class="delta down">+09.84% ↗</span><div class="label">Tenants</div><div class="value">8 Tenants</div>
    <svg class="spark" width="169" height="55" viewBox="0 0 169 55"><path d="M38 55c8-6 10-12 16-14s6-8 12-8 6 4 12-2 6-10 14-10 6 6 12 6 12-20 24-20 18 8 24 12 12-8 17-10V55z" fill="url(#g-orange)"/><path d="M38 55c8-6 10-12 16-14s6-8 12-8 6 4 12-2 6-10 14-10 6 6 12 6 12-20 24-20 18 8 24 12 12-8 17-10" fill="none" stroke="#f7924a" stroke-width="1.6"/></svg></div>
  <div class="stat" style="left:641px"><span class="delta up">+09.84% ↗</span><div class="label">Properties Area</div><div class="value">422,000.00 sq.ft</div>
    <svg class="spark" width="169" height="55" viewBox="0 0 169 55"><path d="M38 55c8-6 10-12 16-14s6-8 12-8 6 4 12-2 6-10 14-10 6 6 12 6 12-20 24-20 18 8 24 12 12-8 17-10V55z" fill="url(#g-violet)"/><path d="M38 55c8-6 10-12 16-14s6-8 12-8 6 4 12-2 6-10 14-10 6 6 12 6 12-20 24-20 18 8 24 12 12-8 17-10" fill="none" stroke="#a66ef5" stroke-width="1.6"/></svg></div>
  <div class="stat" style="left:818px"><span class="delta down">+09.84% ↗</span><div class="label">Rented Area</div><div class="value">233,500.00 sq.ft</div>
    <svg class="spark" width="169" height="55" viewBox="0 0 169 55"><path d="M38 55c8-6 10-12 16-14s6-8 12-8 6 4 12-2 6-10 14-10 6 6 12 6 12-20 24-20 18 8 24 12 12-8 17-10V55z" fill="url(#g-green)"/><path d="M38 55c8-6 10-12 16-14s6-8 12-8 6 4 12-2 6-10 14-10 6 6 12 6 12-20 24-20 18 8 24 12 12-8 17-10" fill="none" stroke="#2ed3a0" stroke-width="1.6"/></svg></div>
  <div class="stat" style="left:996px"><span class="delta up">+09.84% ↗</span><div class="label">Vacancies Area</div><div class="value">188,500.00 sq.ft</div>
    <svg class="spark" width="169" height="55" viewBox="0 0 169 55"><path d="M38 55c8-6 10-12 16-14s6-8 12-8 6 4 12-2 6-10 14-10 6 6 12 6 12-20 24-20 18 8 24 12 12-8 17-10V55z" fill="url(#g-blue)"/><path d="M38 55c8-6 10-12 16-14s6-8 12-8 6 4 12-2 6-10 14-10 6 6 12 6 12-20 24-20 18 8 24 12 12-8 17-10" fill="none" stroke="#22a6f5" stroke-width="1.6"/></svg></div>

  <section class="panel">
    <div class="range">
      <svg width="20" height="20" viewBox="0 0 20 20" fill="none" stroke="#4a5467" stroke-width="1.5"><rect x="1.5" y="3" width="17" height="15" rx="1"/><path d="M1.5 7h17M5 1v4M15 1v4"/><path d="M5 10h2M9 10h2M13 10h2M5 13h2M9 13h2M13 13h2" stroke-width="1.8"/></svg>
      12-27-2021 - 01-03-2021
    </div>
    <span class="chip" style="left:227px">Last 7 days</span>
    <span class="chip" style="left:333px">Last months</span>
    <span class="chip" style="left:439px;width:98px">Last 3 months</span>
    <span class="chip" style="left:545px">Next 7 days</span>
    <span class="chip" style="left:650px">Next months</span>
    <span class="chip" style="left:756px">Next 3 months</span>

    <svg style="position:absolute;left:0;top:0" width="878" height="300" viewBox="0 0 878 300">
      <g stroke="var(--grid)" stroke-width="1">
        <line x1="50" y1="100" x2="848" y2="100"/><line x1="50" y1="134.6" x2="848" y2="134.6"/><line x1="50" y1="169.2" x2="848" y2="169.2"/><line x1="50" y1="203.8" x2="848" y2="203.8"/><line x1="50" y1="238.4" x2="848" y2="238.4"/><line x1="50" y1="273" x2="848" y2="273"/>
      </g>
      <g font-family="Poppins, sans-serif" font-size="7.5" fill="#6b7383" text-anchor="end">
        <text x="40" y="103">10k</text><text x="40" y="138">08k</text><text x="40" y="172">06k</text><text x="40" y="207">04k</text><text x="40" y="241">02k</text><text x="40" y="276">0</text>
      </g>
      <g stroke="#1a9bfc" stroke-width="3" stroke-linecap="round">
        <line x1="62" y1="273" x2="62" y2="183"/><line x1="87.9" y1="273" x2="87.9" y2="221"/><line x1="113.8" y1="273" x2="113.8" y2="254"/><line x1="139.7" y1="273" x2="139.7" y2="176"/><line x1="165.6" y1="273" x2="165.6" y2="216"/><line x1="191.5" y1="273" x2="191.5" y2="197"/><line x1="217.4" y1="273" x2="217.4" y2="254"/><line x1="243.3" y1="273" x2="243.3" y2="152"/><line x1="269.2" y1="273" x2="269.2" y2="268"/><line x1="295.1" y1="273" x2="295.1" y2="216"/><line x1="321" y1="273" x2="321" y2="197"/><line x1="346.9" y1="273" x2="346.9" y2="242"/><line x1="372.8" y1="273" x2="372.8" y2="216"/><line x1="398.7" y1="273" x2="398.7" y2="242"/><line x1="424.6" y1="273" x2="424.6" y2="247"/><line x1="450.5" y1="273" x2="450.5" y2="171"/><line x1="476.4" y1="273" x2="476.4" y2="221"/><line x1="502.3" y1="273" x2="502.3" y2="190"/><line x1="528.2" y1="273" x2="528.2" y2="159"/><line x1="554.1" y1="273" x2="554.1" y2="221"/><line x1="580" y1="273" x2="580" y2="261"/><line x1="605.9" y1="273" x2="605.9" y2="119"/><line x1="631.8" y1="273" x2="631.8" y2="183"/><line x1="657.7" y1="273" x2="657.7" y2="235"/><line x1="683.6" y1="273" x2="683.6" y2="190"/><line x1="709.5" y1="273" x2="709.5" y2="152"/><line x1="735.4" y1="273" x2="735.4" y2="209"/><line x1="761.3" y1="273" x2="761.3" y2="268"/><line x1="787.2" y1="273" x2="787.2" y2="261"/><line x1="813.1" y1="273" x2="813.1" y2="209"/><line x1="839" y1="273" x2="839" y2="235"/>
      </g>
      <g font-family="Poppins, sans-serif" font-size="7.5" fill="#6b7383" text-anchor="middle">
        <text x="62" y="290">01</text><text x="87.9" y="290">02</text><text x="113.8" y="290">03</text><text x="139.7" y="290">04</text><text x="165.6" y="290">05</text><text x="191.5" y="290">06</text><text x="217.4" y="290">07</text><text x="243.3" y="290">08</text><text x="269.2" y="290">09</text><text x="295.1" y="290">10</text><text x="321" y="290">11</text><text x="346.9" y="290">12</text><text x="372.8" y="290">13</text><text x="398.7" y="290">14</text><text x="424.6" y="290">15</text><text x="450.5" y="290">16</text><text x="476.4" y="290">17</text><text x="502.3" y="290">18</text><text x="528.2" y="290">19</text><text x="554.1" y="290">20</text><text x="580" y="290">21</text><text x="605.9" y="290">22</text><text x="631.8" y="290">23</text><text x="657.7" y="290">24</text><text x="683.6" y="290">25</text><text x="709.5" y="290">26</text><text x="735.4" y="290">27</text><text x="761.3" y="290">28</text><text x="787.2" y="290">29</text><text x="813.1" y="290">30</text><text x="839" y="290">31</text>
      </g>
    </svg>

    <span class="legend" style="left:69px;top:312px"><i style="background:#4fc0f8"></i>Scheduled Maintenance</span>
    <span class="legend" style="left:242px;top:312px"><i style="background:#8fd15a"></i>Completed Scheduled Maintenance</span>
    <span class="legend" style="left:479px;top:312px"><i style="background:#f7924a"></i>Future Scheduled Maintenance</span>
    <span class="legend" style="left:690px;top:312px"><i style="background:#f06bb0"></i>Scheduled Work Orders</span>
    <span class="legend" style="left:69px;top:336px"><i style="background:#9aa1ad"></i>Completed Work Orders</span>
    <span class="legend" style="left:242px;top:336px"><i style="background:#f9c74f"></i>Property Inspections in Progress</span>
    <span class="legend" style="left:479px;top:336px"><i style="background:#a66ef5"></i>Completed Property Inspections</span>
    <span class="legend" style="left:690px;top:336px"><i style="background:#2ed3a0"></i>Scheduled Work Orders</span>
  </section>

  <footer class="footer">2019 copyrights © Domora</footer>
</main>
</body>
</html>
```